Automotive eCommerce Business looking for a business card design

Looking for a clean and simple business card design. Our company name is "Brindle Auto" and we are a company specializing in the ecommerce sales of automotive parts, specifically for pick up trucks and large SUVs. Our company colours are red, black, and white.

Feel free to use the logo provided or create a new logo that you seem fit. Looking forward to your creative ideas!

Industry/Entity Type

Automotive

Contact Information for Business Card

We were thinking of a possibly two-sided design featuring just the logo and company name on one side, and personal information on the other side. Single sided designs will be considered as well.

Font styles to use
Serif
Sans Serif
Decorative

Colors
ec1f27
ffffff
000000

Requirements
Must have
• Space for employee's name, title, phone number and email address, along with the company address and website somewhere.

```html
<!DOCTYPE html>
<html lang="en">
<head>
<meta charset="utf-8">
<title>Brindle Auto Ltd. – Business Card</title>
<link rel="stylesheet" href="https://fonts.googleapis.com/css2?family=Cinzel:wght@600&family=Roboto:wght@400;500&family=Roboto+Condensed:wght@700&display=swap">
<style>
  :root {
    --brand-red: #ec1f27;
    --deep-red: #a51d22;
    --card-white: #ffffff;
    --card-black: #1c1c1c;
    --ink-grey: #3c3c3c;
    --soft-grey: #5a5a5a;
    --stage: #2a2a2a;
    --text-light: #f2f2f2;
  }
  * { margin: 0; padding: 0; box-sizing: border-box; }
  html, body {
    width: 1200px; height: 900px; overflow: hidden;
    background: var(--stage);
  }
  .canvas {
    position: relative; width: 1200px; height: 900px;
    display: flex; flex-direction: column; align-items: center; justify-content: center; gap: 30px;
  }
  .card {
    position: relative; width: 640px; height: 366px;
    box-shadow: 0 10px 30px rgba(0,0,0,0.45);
  }
  /* Front */
  .card-front {
    background: var(--card-white);
    display: flex; flex-direction: column; align-items: center; justify-content: center;
  }
  .brand-mark {
    width: 118px; height: 118px; border-radius: 50%;
    background: var(--deep-red); margin-bottom: 26px;
  }
  .brand-name {
    font-family: "Cinzel", serif; font-weight: 600;
    font-size: 30px; color: var(--ink-grey); letter-spacing: 1px;
  }
  .brand-site {
    margin-top: 26px;
    font-family: "Roboto", sans-serif; font-size: 15px;
    letter-spacing: 7px; color: var(--soft-grey);
  }
  /* Back */
  .card-back { background: var(--card-black); color: var(--text-light); }
  .person {
    position: absolute; right: 350px; top: 118px; text-align: right;
  }
  .person-name {
    font-family: "Roboto Condensed", sans-serif; font-weight: 700;
    font-size: 36px; color: var(--brand-red); line-height: 1;
  }
  .person-title {
    font-family: "Roboto", sans-serif; font-weight: 500;
    font-size: 17px; margin-top: 8px; letter-spacing: 0.3px;
  }
  .divider {
    position: absolute; left: 312px; top: 100px; width: 2px; height: 118px;
    background: linear-gradient(to bottom, transparent, #9a9a9a 30%, #9a9a9a 70%, transparent);
  }
  .contact-list {
    position: absolute; left: 336px; top: 104px; list-style: none;
    font-family: "Roboto", sans-serif; font-weight: 500; font-size: 16px;
  }
  .contact-list li { display: flex; align-items: center; gap: 10px; height: 22px; }
  .contact-list svg { width: 14px; height: 14px; fill: var(--brand-red); flex: none; }
  .address {
    position: absolute; left: 150px; bottom: 58px;
    display: flex; align-items: center; gap: 6px;
    font-family: "Roboto", sans-serif; font-weight: 500; font-size: 17px;
  }
  .address svg { width: 14px; height: 18px; fill: var(--brand-red); }
</style>
</head>
<body>
<main class="canvas">
  <section class="card card-front">
    <div class="brand-mark"></div>
    <h1 class="brand-name">Brindle Auto Ltd.</h1>
    <p class="brand-site">www.brindleauto.com</p>
  </section>

  <section class="card card-back">
    <div class="person">
      <h2 class="person-name">MARCUS HALE</h2>
      <p class="person-title">CEO/FOUNDER</p>
    </div>
    <div class="divider"></div>
    <ul class="contact-list">
      <li><svg viewBox="0 0 24 24"><path d="M6.6 10.8a15.1 15.1 0 0 0 6.6 6.6l2.2-2.2a1 1 0 0 1 1-.25 11.4 11.4 0 0 0 3.6.57 1 1 0 0 1 1 1V20a1 1 0 0 1-1 1A17 17 0 0 1 3 4a1 1 0 0 1 1-1h3.5a1 1 0 0 1 1 1c0 1.25.2 2.45.57 3.57a1 1 0 0 1-.25 1z"/></svg>555 210 4873</li>
      <li><svg viewBox="0 0 24 24"><path d="M7 1h10a2 2 0 0 1 2 2v18a2 2 0 0 1-2 2H7a2 2 0 0 1-2-2V3a2 2 0 0 1 2-2zm0 3v14h10V4zm5 15.5a1.2 1.2 0 1 0 0 2.4 1.2 1.2 0 0 0 0-2.4z"/></svg>555 318 6290</li>
      <li><svg viewBox="0 0 24 24"><path d="M6 2h12v5H6zM4 8h16a2 2 0 0 1 2 2v7h-4v5H6v-5H2v-7a2 2 0 0 1 2-2zm4 7v5h8v-5z"/></svg>555 742 1086</li>
      <li><svg viewBox="0 0 24 24"><path d="M2 5h20v14H2zm2 2v.5l8 5.5 8-5.5V7z"/></svg>mail@brindleauto.com</li>
      <li><svg viewBox="0 0 24 24"><path d="M12 2a10 10 0 1 0 0 20 10 10 0 0 0 0-20zm0 2a8 8 0 0 1 7.9 7H4.1A8 8 0 0 1 12 4zm-7.9 9h15.8a8 8 0 0 1-15.8 0z"/></svg>www.brindleauto.com</li>
    </ul>
    <p class="address"><svg viewBox="0 0 24 30"><path d="M12 0a10 10 0 0 0-10 10c0 7.5 10 20 10 20s10-12.5 10-20A10 10 0 0 0 12 0zm0 14a4 4 0 1 1 0-8 4 4 0 0 1 0 8z"/></svg>1420 Cedar Ridge Road, Juneau, Alaska 99801</p>
  </section>
</main>
</body>
</html>
```